Tallreed Agency Website

We need a website design for a UK based marketing and PR agency called "Tallreed Agency". We are a small and vibrant team that looks after a mixture of clients from the luxury lifestyle and professional services sectors so the design needs to reflect this and convey: Professionalism, contemporary approach, creativity and the high end luxury and professional market we look after. Our services include marketing, PR, social media and copywriting and we look after both local and national clients. The design will need to incorporate the grey and orange brand colours (logo attached) but we are open to the use of more/different colours - with the possibility of a slight refresh on the current logo/branding. The main pages required include: Home, About Us, Services, Sectors, Case Studies and Blog.

ur existing website can be seen here - http://www.tallreed-example.co.uk

The site will need to showcase our approach, services and expertise, existing/previous clients, and provide frequently updated content via news and blog to support our marketing campaigns.

The key objectives for the site are:
- To support current sales activity by giving potential clients somewhere to visit to find out who we are, what we can do, what we have done
- To generate incoming sales leads/enquiries from companies looking for marketing and PR services
- To showcase us as a high end a professional agency with some fantastic clients and a wealth of experience

Target Market(s)

Professional services e.g. accountants, data centres etc
Luxury lifestyle e.g. wedding venue, tailor, homeware etc.
British market - mainly South East/London
Small - Medium sized businesses

Industry/Entity Type

Marketing

Font styles to use
Other font styles liked:
• Din Regular and Bold is currently used

Colors
f78f20
aaaaaa

Requirements
Must have
• Must Have:
- The main menu items are likely to be:
- Services
- Sectors
- About us
- Case Studies
- Blog
- Contact us

Some of these items may have a sub-menu, e.g. About us is likely to have "Company", "Team", and "Careers" below it and "Services" will have "marketing", "PR", "Copywriting", "Social media". Sectors will have "Professional", "Luxury", "Lifestyle"

Key must-have elements of the homepage include:
- Social media icons (twitter, linkedin, facebook, google+)
- Contact details (i.e. phone number and email/link)
- "We have worked with..." - this is likely to be icons for logos of previous and current clients
- "Sign up to newsletter"
- "Latest news"

Footer navigation must allow for the usual suspects (sitemap, t's & c's, privacy policy, company registration details)

Some kind of call-to-action boxes/areas/links to provide us with ways to link out to any specific micro-sites or pages within the site (e.g. to highlight some of our specific case studies, services etc).

To confirm, we are looking for the following page types/templates:
1) Home page
2) Inside/content page (can be used for services, about us etc)
3) Article page (for blog/news articles etc)
4) Case studies (an image led pad to showcase campaigns we have worked on)
4) Contact page
Nice to have
• - If web fonts are needed for the design, then please note we have an existing web fonts account with typevault-example.com and so can use any of the web fonts available there.
Should not have
• We do not want to use a one page-scroll down website

```html
<!DOCTYPE html>
<html lang="en">
<head>
<meta charset="utf-8">
<title>Tallreed Agency</title>
<link href="https://fonts.googleapis.com/css2?family=Lato:wght@300;400;700;900&display=swap" rel="stylesheet">
<style>
:root{
  --orange:#f78f20;
  --grey:#aaaaaa;
  --ink:#333333;
  --text:#555555;
  --muted:#999999;
  --light:#f1f1f1;
  --white:#ffffff;
  --dark:#2f2f2f;
  --darker:#262626;
  --footer:#383838;
}
*{box-sizing:border-box;margin:0;padding:0}
html,body{width:1200px;height:2828px;overflow:hidden}
body{font-family:"Lato",sans-serif;color:var(--text);background:var(--white)}
a{color:inherit;text-decoration:none}

/* header */
.site-header{height:96px;background:var(--dark);display:flex;align-items:center;justify-content:space-between;padding:0 160px}
.brand{display:flex;align-items:center;gap:12px;font-size:26px;font-weight:700;color:var(--orange)}
.brand-mark{width:14px;height:14px;background:var(--orange)}
.main-nav{display:flex;height:96px}
.main-nav a{display:flex;align-items:center;padding:0 20px;font-size:15px;color:#ddd}
.main-nav a.active{background:#1c1c1c;color:var(--white);font-weight:700}

/* hero */
.hero{position:relative;height:394px;overflow:hidden}
.hero-photo{position:absolute;inset:0;background:linear-gradient(100deg,#d9d6d2 0%,#f4f2ef 35%,#fbfaf8 60%,#e8dfe2 85%,#d9cfd3 100%)}
.hero-content{position:relative;text-align:center;padding-top:102px}
.hero h1{font-size:46px;font-weight:900;color:#2a2a2a;letter-spacing:1px}
.hero p{width:560px;margin:24px auto 0;font-size:15px;line-height:22px;color:#555}

/* section shared */
.section{text-align:center}
.section-grey{background:var(--light)}
.section-title{display:flex;align-items:center;justify-content:center;gap:28px;font-size:26px;font-weight:900;color:var(--ink);letter-spacing:1px}
.section-title::before,.section-title::after{content:"";width:130px;height:2px;background:#bcbcbc}

/* services */
.services{height:442px;padding-top:38px}
.service-list{display:flex;justify-content:center;gap:50px;margin-top:50px}
.service{width:180px}
.service-image{width:112px;height:112px;border-radius:50%;margin:0 auto;border:4px solid #e0e0e0}
.service h3{margin-top:30px;font-size:16px;font-weight:700;color:var(--ink)}
.service.highlight h3{color:var(--orange)}
.service p{margin-top:12px;font-size:12px;line-height:18px;color:var(--muted)}

/* testimonials */
.testimonials{height:468px;padding-top:28px}
.quote-badge{width:56px;height:56px;border-radius:50%;background:#c9c9c9;margin:58px auto 0;display:flex;align-items:center;justify-content:center}
.quote-text{margin:44px auto 0;width:840px;font-size:30px;line-height:40px;color:#777;font-weight:700}
.quote-text strong{color:#555;font-weight:900}
.quote-author{margin-top:12px;font-size:18px;color:var(--muted)}
.slider-dots{display:flex;justify-content:center;gap:10px;margin-top:84px}
.slider-dots span{width:12px;height:12px;border-radius:50%;background:#ccc}
.slider-dots span.on{background:#888}

/* team */
.team{height:440px;padding-top:46px}
.team-list{display:flex;justify-content:center;gap:60px;margin-top:42px}
.member{width:180px}
.member-photo{width:108px;height:108px;border-radius:50%;margin:0 auto;border:4px solid var(--white)}
.member h3{margin-top:20px;font-size:14px;font-weight:700;color:var(--ink)}
.member.highlight h3{color:var(--orange)}
.member .role{font-size:12px;color:var(--muted);margin-top:2px}
.member p{margin-top:10px;font-size:12px;line-height:17px;color:var(--muted)}
.member-social{display:flex;justify-content:center;gap:8px;margin-top:10px}
.member-social span{width:12px;height:12px;border-radius:50%;background:#bdbdbd}

/* work */
.work{height:580px;padding-top:46px}
.work-filter{display:flex;justify-content:center;gap:6px;margin-top:36px}
.work-filter span{padding:8px 18px;font-size:13px;color:var(--text);background:#eee}
.work-filter span.active{background:var(--orange);color:var(--white)}
.work-grid{display:grid;grid-template-columns:repeat(3,292px);grid-template-rows:repeat(2,186px);width:876px;margin:30px auto 0;gap:0 0;position:relative;left:-2px}
.work-item{position:relative;background:linear-gradient(180deg,#c9c4bd 0%,#b3aaa2 45%,#8c7f7a 100%)}
.work-item.tint{background:linear-gradient(180deg,#c6c0bc 0%,#b49ea0 50%,#8a6f74 100%)}
.work-overlay{position:absolute;inset:0;background:rgba(30,30,30,.72);display:flex;flex-direction:column;align-items:center;justify-content:center;color:var(--white)}
.work-overlay .icon{width:40px;height:40px;border-radius:50%;background:var(--orange);display:flex;align-items:center;justify-content:center;margin-bottom:12px}
.work-overlay h4{font-size:14px;font-weight:700}
.work-overlay small{font-size:11px;color:#ccc;margin-top:3px}

/* connect bar */
.connect-bar{height:48px;background:var(--darker);display:flex;align-items:center;justify-content:space-between;padding:0 160px;color:#ccc;font-size:14px}
.social-links{display:flex;gap:22px}
.social-links span{width:18px;height:18px;border-radius:50%;background:#6a6a6a}

/* footer */
.site-footer{height:304px;background:var(--footer);padding:30px 160px 0;display:grid;grid-template-columns:220px 230px 230px 200px;gap:0 20px;color:#aaa;font-size:12px;line-height:20px}
.site-footer h5{color:var(--white);font-size:15px;font-weight:700;margin-bottom:16px}
.contact-table{display:grid;grid-template-columns:56px 1fr}
.contact-table .lnk{color:var(--orange)}
.signup-input{margin-top:12px;height:28px;width:180px;background:var(--white)}
.signup-button{margin-top:8px;margin-left:100px;width:90px;height:26px;background:#1f1f1f;color:#ddd;font-size:11px;font-weight:700;display:flex;align-items:center;justify-content:center}
.blog-post{display:flex;gap:12px}
.blog-thumb{width:44px;height:44px;border-radius:50%;flex:none;background:linear-gradient(135deg,#b8aca2,#7e706a)}
.blog-post h6{color:var(--white);font-size:12px;font-weight:700;line-height:16px}
.blog-post .more{color:var(--orange);font-weight:700}

/* bottom bar */
.bottom-bar{height:56px;background:#2a2a2a;display:flex;align-items:center;justify-content:space-between;padding:0 160px;font-size:11px;color:#888}
.bottom-links{display:flex;gap:20px}
</style>
</head>
<body>

<header class="site-header">
  <div class="brand"><span class="brand-mark"></span>Tallreed Agency</div>
  <nav class="main-nav">
    <a class="active" href="#">Home</a>
    <a href="#">About Us</a>
    <a href="#">Services</a>
    <a href="#">Sectors</a>
    <a href="#">Case Studies</a>
    <a href="#">Blog</a>
    <a href="#">Contact Us</a>
  </nav>
</header>

<section class="hero">
  <div class="hero-photo" role="img" aria-label="Bright photo of an elegant event table with glassware and flowers"></div>
  <div class="hero-content">
    <h1>MAKE YOUR EVENTS AMAZING</h1>
    <p>Etiam rhoncus. Maecenas tempus, tellus eget condimentum rhoncus, sem quam semper libero, sit amet adipiscing sem neque sed ipsum.</p>
  </div>
</section>

<section class="section section-grey services">
  <h2 class="section-title">SERVICES</h2>
  <div class="service-list">
    <div class="service">
      <div class="service-image" role="img" aria-label="Marketing sketch illustration" style="background:linear-gradient(135deg,#e4e4e4,#bdbdbd)"></div>
      <h3>Marketing</h3>
      <p>Phasellus viverra nulla ut metus varius laoreet. Quisque rutrum aenean imperdiet.</p>
    </div>
    <div class="service highlight">
      <div class="service-image" role="img" aria-label="PR service photo" style="background:linear-gradient(135deg,#9a9a9a,#4d4d4d)"></div>
      <h3>PR Service</h3>
      <p>Phasellus viverra nulla ut metus varius laoreet. Quisque rutrum aenean imperdiet.</p>
    </div>
    <div class="service">
      <div class="service-image" role="img" aria-label="Social media icons collage" style="background:linear-gradient(135deg,#b9c6dc,#5a77a8)"></div>
      <h3>Social Media</h3>
      <p>Phasellus viverra nulla ut metus varius laoreet. Quisque rutrum aenean imperdiet.</p>
    </div>
    <div class="service">
      <div class="service-image" role="img" aria-label="Copywriting typewriter photo" style="background:linear-gradient(135deg,#dfe6ea,#a9b6bd)"></div>
      <h3>Copywriting</h3>
      <p>Phasellus viverra nulla ut metus varius laoreet. Quisque rutrum aenean imperdiet.</p>
    </div>
  </div>
</section>

<section class="section testimonials">
  <h2 class="section-title">THEY SAYS</h2>
  <div class="quote-badge">
    <svg width="24" height="20" viewBox="0 0 24 20"><path d="M0 20V11C0 5 3 1 9 0v4c-3 1-4 3-4 6h4v10zM14 20V11c0-6 3-10 9-11v4c-3 1-4 3-4 6h4v10z" fill="#fff"/></svg>
  </div>
  <p class="quote-text">Lorem ipsum dolor sit amet, consectetuer adipiscing elit. Aenean commodo ligula eget dolor. <strong>Aenean massa.</strong></p>
  <p class="quote-author">Any Customer</p>
  <div class="slider-dots"><span class="on"></span><span></span><span></span></div>
</section>

<section class="section section-grey team">
  <h2 class="section-title">OUR TEAM</h2>
  <div class="team-list">
    <div class="member">
      <div class="member-photo" role="img" aria-label="Portrait of team member" style="background:#cfcfcf"></div>
      <h3>Jenna Stowell</h3><div class="role">Web Design</div>
      <p>Phasellus viverra nulla ut metus varius laoreet quisque rutrum.</p>
      <div class="member-social"><span></span><span></span><span></span></div>
    </div>
    <div class="member highlight">
      <div class="member-photo" role="img" aria-label="Portrait of team member" style="background:#c7a692"></div>
      <h3>Peter Rowland</h3><div class="role">Web Design</div>
      <p>Phasellus viverra nulla ut metus varius laoreet quisque rutrum.</p>
      <div class="member-social"><span></span><span></span><span></span></div>
    </div>
    <div class="member">
      <div class="member-photo" role="img" aria-label="Portrait of team member" style="background:#bdbdbd"></div>
      <h3>Jenna Stowell</h3><div class="role">Web Design</div>
      <p>Phasellus viverra nulla ut metus varius laoreet quisque rutrum.</p>
      <div class="member-social"><span></span><span></span><span></span></div>
    </div>
    <div class="member">
      <div class="member-photo" role="img" aria-label="Portrait of team member" style="background:#d3d3d3"></div>
      <h3>Jenna Stowell</h3><div class="role">Web Design</div>
      <p>Phasellus viverra nulla ut metus varius laoreet quisque rutrum.</p>
      <div class="member-social"><span></span><span></span><span></span></div>
    </div>
  </div>
</section>

<section class="section work">
  <h2 class="section-title">OUR WORK</h2>
  <div class="work-filter"><span>All</span><span class="active">PR</span><span>Events</span><span>Web Design</span></div>
  <div class="work-grid">
    <div class="work-item" role="img" aria-label="Exhibition event photo"></div>
    <div class="work-item tint" role="img" aria-label="Exhibition event photo">
      <div class="work-overlay">
        <div class="icon"><svg width="16" height="16" viewBox="0 0 16 16"><path d="M8 2v12M2 8h12" stroke="#fff" stroke-width="2.5"/></svg></div>
        <h4>Ayan Ikes Lorem Sans</h4>
        <small>Event Press Launch</small>
      </div>
    </div>
    <div class="work-item" role="img" aria-label="Exhibition event photo"></div>
    <div class="work-item" role="img" aria-label="Exhibition event photo"></div>
    <div class="work-item tint" role="img" aria-label="Exhibition event photo"></div>
    <div class="work-item" role="img" aria-label="Exhibition event photo"></div>
  </div>
</section>

<div class="connect-bar">
  <span>Let's Connect</span>
  <div class="social-links"><span></span><span></span><span></span><span></span><span></span></div>
</div>

<footer class="site-footer">
  <div>
    <h5>Contact Us</h5>
    <p>Lorem Grand Place<br>12 Reedgate, Kent Road<br>KT1 4RE</p>
  </div>
  <div style="padding-top:36px">
    <div class="contact-table">
      <span>Phone</span><span>01632 960 221</span>
      <span>Fax</span><span>01632 960 222</span>
      <span>Email</span><span class="lnk">info@tallreed-example.co.uk</span>
    </div>
  </div>
  <div>
    <h5>Newsletter Signup</h5>
    <p>Phasellus viverra nulla ut metus varius laoreet quisque rutrum.</p>
    <div class="signup-input"></div>
    <div class="signup-button">SUBSCRIBE</div>
  </div>
  <div>
    <h5>Latest From Blog</h5>
    <div class="blog-post">
      <div class="blog-thumb" role="img" aria-label="Blog post thumbnail"></div>
      <div>
        <h6>Lorem ipsum dolor sit amet consectetur</h6>
        <p>Quisque rutrum aenean imperdiet etiam.</p>
        <span class="more">Read More</span>
      </div>
    </div>
  </div>
</footer>

<div class="bottom-bar">
  <span>© 2014 Tallreed Agency</span>
  <div class="bottom-links"><span>Home</span><span>Terms of Service</span><span>Terms &amp; Conditions</span><span>Privacy</span><span>Sitemap</span><span>Contact Us</span></div>
</div>

</body>
</html>
```